RW Framewell Inc Business cards

We need business cards using our existing logo but slightly modified. Right now the logo says RW Loadbearing Masonry. We want to keep the RW part of the design, but replace the Structural Concrete portion with "FRAMEWELL". Please see the attached file.
Ideally this would be a blank template so we can add Different Names, titles, and phone numbers later.
On the one side we want only the logo and on the other side the detail. I'm attaching an example for you to see.
Please reach out with any other questions. Our address and other details will be given out once we find a design we like.

Target Market(s)

Construction Industry

```html
<!DOCTYPE html>
<html lang="en">
<head>
<meta charset="utf-8">
<title>RW Framewell Inc — Business Cards</title>
<link rel="stylesheet" href="https://fonts.googleapis.com/css2?family=Michroma&family=Open+Sans:wght@400&display=swap">
<style>
  :root {
    --brand-blue: #1a74bf;
    --paper: #ffffff;
    --ink-grey: #6a6a6a;
    --backdrop: #e9e6e1;
  }
  * { box-sizing: border-box; margin: 0; padding: 0; }
  html, body {
    width: 1200px; height: 859px; overflow: hidden;
    background: var(--backdrop);
  }
  .canvas { position: relative; width: 1200px; height: 859px; }
  .card {
    position: absolute; top: 287px;
    width: 500px; height: 285px;
    background: var(--paper);
    overflow: hidden;
    box-shadow: 0 6px 14px rgba(0,0,0,0.25);
  }
  .card--details { left: 60px; }
  .card--brand { left: 640px; background: var(--brand-blue); }

  .card__graphic { position: absolute; }
  .card--details .card__graphic {
    left: 312px; top: 33px; width: 188px; height: 246px;
    background: linear-gradient(135deg, var(--paper) 0%, var(--brand-blue) 60%);
  }
  .card--brand .card__graphic {
    left: 0; top: 33px; width: 150px; height: 246px;
    background: linear-gradient(45deg, var(--paper) 0%, var(--brand-blue) 85%);
  }
  .card__stripe {
    position: absolute; left: 0; bottom: 0; width: 100%; height: 6px;
  }
  .card--details .card__stripe { background: var(--brand-blue); }
  .card--brand .card__stripe { background: var(--paper); }

  .wordmark {
    position: absolute; display: flex; align-items: center; gap: 8px;
    font-family: "Michroma", sans-serif; font-weight: 400;
    letter-spacing: 0.5px; white-space: nowrap;
  }
  .wordmark__square { display: block; background: currentColor; }
  .card--details .wordmark { left: 19px; top: 23px; font-size: 21px; color: var(--brand-blue); }
  .card--details .wordmark__square { width: 16px; height: 16px; }
  .card--brand .wordmark { left: 160px; top: 118px; font-size: 24px; color: var(--paper); }
  .card--brand .wordmark__square { width: 18px; height: 18px; }

  .person__name {
    position: absolute; left: 19px; top: 143px;
    font-family: "Michroma", sans-serif; font-size: 17px; font-weight: 400;
    color: var(--brand-blue); letter-spacing: 0.5px;
  }
  .person__title {
    position: absolute; left: 19px; top: 163px;
    font-family: "Open Sans", sans-serif; font-size: 13px; color: var(--ink-grey);
  }
  .contact-list {
    position: absolute; left: 19px; top: 203px; list-style: none;
    font-family: "Open Sans", sans-serif; font-size: 13px; color: var(--ink-grey);
  }
  .contact-list li { display: flex; align-items: center; height: 17px; }
  .contact-list svg { width: 12px; height: 12px; margin-right: 7px; fill: var(--brand-blue); }
  .address {
    position: absolute; right: 15px; top: 238px; text-align: right;
    font-family: "Open Sans", sans-serif; font-size: 13px; line-height: 17px;
    color: var(--paper);
  }
  .web-link {
    position: absolute; right: 45px; top: 255px;
    font-family: "Open Sans", sans-serif; font-size: 13px; color: var(--paper);
  }
</style>
</head>
<body>
<main class="canvas">

  <section class="card card--details" aria-label="Business card, contact side">
    <div class="card__graphic" role="img" aria-label="Angled blue and white graphic panel"></div>
    <div class="card__stripe"></div>

    <div class="wordmark"><span class="wordmark__square"></span>RW FRAMEWELL</div>

    <h1 class="person__name">DANA MILLER</h1>
    <p class="person__title">Chief Officer</p>

    <ul class="contact-list">
      <li><svg viewBox="0 0 24 24"><path d="M6.6 10.8a15 15 0 0 0 6.6 6.6l2.2-2.2a1 1 0 0 1 1-.25 11.4 11.4 0 0 0 3.6.57 1 1 0 0 1 1 1V20a1 1 0 0 1-1 1A17 17 0 0 1 3 4a1 1 0 0 1 1-1h3.5a1 1 0 0 1 1 1c0 1.25.2 2.45.57 3.57a1 1 0 0 1-.25 1z"/></svg>+00 7 41 00 00</li>
      <li><svg viewBox="0 0 24 24"><path d="M7 1h10a2 2 0 0 1 2 2v18a2 2 0 0 1-2 2H7a2 2 0 0 1-2-2V3a2 2 0 0 1 2-2zm0 3v14h10V4zm5 15.5a1 1 0 1 0 0 2 1 1 0 0 0 0-2z"/></svg>+00 0 62 00 00</li>
      <li><svg viewBox="0 0 24 24"><path d="M2 5h20v14H2zm2 2v.5l8 5 8-5V7zm0 3v7h16v-7l-8 5z"/></svg>info@rwframewell.com</li>
      <li><svg viewBox="0 0 24 24"><path d="M12 2a10 10 0 1 0 0 20 10 10 0 0 0 0-20zm-1 2.1V8H7.3A8 8 0 0 1 11 4.1zm2 0A8 8 0 0 1 16.7 8H13zM4.5 10H11v4H4.5a8 8 0 0 1 0-4zm8.5 0h6.5a8 8 0 0 1 0 4H13zm-5.7 6H11v3.9A8 8 0 0 1 7.3 16zm5.7 0h3.7a8 8 0 0 1-3.7 3.9z"/></svg>www.rwframewell.com</li>
    </ul>

    <p class="address">Your address line here<br>Country/ State</p>
  </section>

  <section class="card card--brand" aria-label="Business card, logo side">
    <div class="card__graphic" role="img" aria-label="Angled white and blue graphic panel"></div>
    <div class="card__stripe"></div>

    <div class="wordmark"><span class="wordmark__square"></span>RW FRAMEWELL</div>

    <p class="web-link">www.rwframewell.com</p>
  </section>

</main>
</body>
</html>
```